Business Card: RW Office Partners - Your organised problem solver

Business Name: RW Office Partners
Website: www.rwofficepartners.com.au
Email: marisol@rwofficepartners.com.au
Mobile: 61 482 907 236
Facebook: @rwofficepartners
Instrgram: @rwofficepartners

Brading Colours:
HEX
#986474
#ddccd3
#7a8498
#c9d8e4
#000000
#ffffff

Tag Line: Your steady task organiser

Link to DRAFT website:
https://deskhelpcollective.wixsite.com/rw-office-partners

About Page from the website:
My name is Marisol Wrenfield, and I would love to assist you to become more productive in your day to day and achieve your business and personal goals.
My mission is to give you time, time to work on the important tasks of your business or to be able to spend more time with your family. I will take on the tasks you don’t have time for, don’t know well or simply don’t like to do.
I have an extensive background in Administration, Tender Coordination, Document Control, WHS and Quality Management working primarily in the Construction, Mining and Corporate World.
I am passionate about being organised, having order and making things in your life (and mine) easier! I love to watch something unfold and grow into something amazing! I am known for being the go-to problem solver, the organiser of all things, producing high standards of work even under pressure. I’m also a confident communicator, and I understand that you’re busy running your business.

Target Market(s)

Small to Medium Business who require assistance in their business by a virtual assistant.

Industry/Entity Type

Virtual Assistant

Contact Information for Business Card

Mobile: 61 482 907 236

Font styles to use
Sans Serif

Colors
ffffff

Requirements
Must have
• Branding Colours as outlined.
Contact Details as outlined.
Logo as provided.
Proper contact details - mobile, facebook, instragm, website.
Simple, Elegant, very clean looking.
Should not have
• Note cute with pictures.
Not too girly as still want to market to construction companies.

```html
<!DOCTYPE html>
<html lang="en">
<head>
<meta charset="utf-8">
<title>RW Office Partners – Business Card</title>
<link rel="stylesheet" href="https://fonts.googleapis.com/css2?family=Montserrat:wght@500&family=Roboto:wght@400;700&family=Kalam&display=swap">
<style>
  :root {
    --backdrop: #3b3b3d;
    --card-black: #1c1b1e;
    --mauve: #8a5a6d;
    --mauve-light: #986474;
    --slate: #7a8498;
    --logo-grey: #6f6f74;
    --white: #ffffff;
  }
  * { margin: 0; padding: 0; box-sizing: border-box; }
  html, body { width: 799px; height: 1200px; overflow: hidden; }
  body {
    background: var(--backdrop);
    font-family: "Roboto", Arial, sans-serif;
    position: relative;
  }
  .card {
    position: absolute;
    left: 70px;
    width: 660px;
    height: 377px;
    background: var(--card-black);
    border-radius: 4px;
    overflow: hidden;
    box-shadow: 0 14px 30px rgba(0,0,0,.45);
  }
  .card--front { top: 150px; }
  .card--back { top: 680px; }

  .wordmark {
    font-family: "Montserrat", Arial, sans-serif;
    font-weight: 500;
    text-transform: uppercase;
    letter-spacing: 1px;
    position: absolute;
    line-height: .95;
    white-space: nowrap;
  }
  .card--front .wordmark {
    color: var(--logo-grey);
    font-size: 58px;
    left: 150px;
    top: 80px;
  }
  .socials {
    position: absolute;
    left: 150px;
    top: 262px;
    display: flex;
    gap: 26px;
    color: var(--white);
    font-size: 17px;
  }
  .social { display: flex; align-items: center; gap: 8px; }
  .social-mark {
    width: 13px; height: 13px;
    background: var(--mauve-light);
  }
  .social-mark--round { border-radius: 50%; }
  .social-mark--square { border-radius: 2px; }

  .card--back .wordmark {
    color: var(--mauve-light);
    font-size: 30px;
    left: 36px;
    top: 34px;
  }
  .tagline {
    position: absolute;
    left: 40px;
    top: 110px;
    font-family: "Kalam", cursive;
    color: var(--white);
    font-size: 19px;
    letter-spacing: .5px;
  }
  .wave { position: absolute; left: 0; top: 0; width: 660px; height: 377px; }

  .contact-block {
    position: absolute;
    right: 34px;
    top: 198px;
    text-align: right;
    color: var(--white);
  }
  .person-name { font-weight: 700; font-size: 22px; letter-spacing: .5px; }
  .person-role { font-size: 15px; margin-bottom: 14px; color: #eee; }
  .contact-list { list-style: none; }
  .contact-item {
    display: flex; justify-content: flex-end; align-items: center;
    gap: 10px; font-size: 15px; line-height: 21px;
  }
  .contact-icon { width: 14px; height: 14px; flex: none; }
</style>
</head>
<body>

<section class="card card--front" aria-label="Card front">
  <div class="wordmark">RW Office<br>Partners</div>
  <div class="socials">
    <span class="social"><span class="social-mark social-mark--square"></span>@rwofficepartners</span>
    <span class="social"><span class="social-mark social-mark--round"></span>@rwofficepartners</span>
  </div>
</section>

<section class="card card--back" aria-label="Card back">
  <svg class="wave" viewBox="0 0 660 377" aria-hidden="true">
    <path d="M0 160 C 150 150, 260 215, 420 185 S 600 120, 660 150 L660 377 L0 377 Z" fill="#101012"/>
    <path d="M0 168 C 150 158, 260 220, 420 192 S 600 130, 660 160 L660 377 L0 377 Z" fill="var(--slate)"/>
    <path d="M0 178 C 150 172, 260 232, 420 204 S 600 145, 660 172 L660 377 L0 377 Z" fill="#101012"/>
    <path d="M0 186 C 150 182, 260 240, 420 214 S 600 158, 660 182 L660 377 L0 377 Z" fill="var(--mauve)"/>
  </svg>
  <div class="wordmark">RW Office<br>Partners</div>
  <p class="tagline">Your steady task organiser</p>

  <div class="contact-block">
    <p class="person-name">Marisol Wrenfield</p>
    <p class="person-role">Virtual Assistant</p>
    <ul class="contact-list">
      <li class="contact-item">61 482 907 236
        <svg class="contact-icon" viewBox="0 0 16 16"><path d="M3 1h3l1.5 4-2 1.2a9 9 0 0 0 4.3 4.3L11 8.5l4 1.5v3a2 2 0 0 1-2 2A12 12 0 0 1 1 3a2 2 0 0 1 2-2z" fill="#fff"/></svg>
      </li>
      <li class="contact-item">@rwofficepartners
        <svg class="contact-icon" viewBox="0 0 16 16"><rect x="1" y="1" width="14" height="14" rx="3" fill="#fff"/></svg>
      </li>
      <li class="contact-item">@rwofficepartners
        <svg class="contact-icon" viewBox="0 0 16 16"><circle cx="8" cy="8" r="7" fill="#fff"/></svg>
      </li>
      <li class="contact-item">www.rwofficepartners.com.au
        <svg class="contact-icon" viewBox="0 0 16 16" fill="none" stroke="#fff" stroke-width="1.4"><circle cx="8" cy="8" r="6.5"/><ellipse cx="8" cy="8" rx="3" ry="6.5"/><path d="M1.5 8h13"/></svg>
      </li>
      <li class="contact-item">marisol@rwofficepartners.com.au
        <svg class="contact-icon" viewBox="0 0 16 16"><rect x="1" y="3" width="14" height="10" rx="1" fill="#fff"/><path d="M1.5 3.8 8 9l6.5-5.2" fill="none" stroke="var(--mauve)" stroke-width="1.3"/></svg>
      </li>
    </ul>
  </div>
</section>

</body>
</html>
```